Website for new crypto research organization

See brief (attached). This is a pretty basic website with only a handful of pages + ability to collect email addresses.

```html
<!DOCTYPE html>
<html lang="en">
<head>
<meta charset="utf-8">
<title>Tealstone Research</title>
<link href="https://fonts.googleapis.com/css2?family=Lato:wght@400;700;900&family=Roboto:wght@400;500&display=swap" rel="stylesheet">
<style>
:root{
  --teal:#1a9c98;
  --teal-dark:#158682;
  --blue:#1e9bd0;
  --ink:#111111;
  --text:#333333;
  --muted:#555555;
  --white:#ffffff;
  --black:#000000;
}
*{box-sizing:border-box;margin:0;padding:0}
html,body{width:1200px;height:3561px;overflow:hidden;background:var(--white)}
body{position:relative;font-family:"Roboto",sans-serif;color:var(--text)}
a{color:inherit;text-decoration:none}
.abs{position:absolute}

/* top bar */
.topbar{left:0;top:0;width:1200px;height:47px;background:var(--teal);color:var(--white);font-family:"Lato",sans-serif;font-size:17px;font-weight:700}
.topbar .follow{left:110px;top:12px;display:flex;align-items:center;gap:8px}
.ring{display:inline-block;width:30px;height:30px;border:2px solid var(--white);border-radius:50%}
.topbar .email{left:405px;top:14px}
.topbar .email span{font-weight:400;font-size:15px}
.topbar .call{right:113px;top:14px}
.topbar .call span{font-weight:400;font-size:15px}

/* nav */
.nav{left:0;top:47px;width:1200px;height:91px;background:var(--white)}
.brand{left:110px;top:15px;width:109px;height:62px;border:2px solid var(--teal);display:flex;align-items:center;justify-content:center;text-align:center;color:var(--teal);font-family:"Lato",sans-serif;font-weight:700;font-size:13px;line-height:1.1}
.menu{left:332px;top:33px;display:flex;gap:0;font-size:15px;color:var(--ink)}
.menu a{margin-right:48px}
.menu a.active{color:var(--teal);position:relative}
.menu a.active::after{content:"";position:absolute;left:14px;right:14px;top:24px;height:2px;background:var(--teal);box-shadow:0 4px 0 var(--teal)}
.search{left:897px;top:33px}
.login{left:965px;top:22px;width:118px;height:42px;background:var(--teal);color:var(--white);border-radius:0 18px 0 18px;font-size:15px;font-weight:500;display:flex;align-items:center;justify-content:center;gap:6px}

/* hero */
.hero{left:0;top:138px;width:1200px;height:643px;background:radial-gradient(circle at 78% 40%,#1c6e6c 0%,#0f3a40 22%,#0b1d26 48%,#070d14 100%);border-bottom-right-radius:240px 330px;overflow:hidden}
.hero h1{position:absolute;left:111px;top:178px;color:var(--white);font-family:"Lato",sans-serif;font-weight:700;font-size:43px;line-height:50px;letter-spacing:.5px}
.hero p{position:absolute;left:111px;top:290px;width:440px;color:var(--white);font-size:14.5px;line-height:28px}
.hero .cta{position:absolute;left:113px;top:394px;width:152px;height:42px;background:var(--teal);color:var(--white);border-radius:0 20px 0 20px;font-size:15px;font-weight:500;display:flex;align-items:center;justify-content:center}
.arrow{position:absolute;width:40px;height:40px;border-radius:50%;background:var(--blue);display:flex;align-items:center;justify-content:center}

/* headings */
.sec-title{left:0;width:1200px;text-align:center;color:var(--teal);font-family:"Lato",sans-serif;font-weight:700;font-size:31px;letter-spacing:.5px}
.sec-title::after{content:"";display:block;width:116px;height:3px;background:var(--teal);margin:12px auto 0}

/* research cards */
.research{left:110px;top:947px;width:977px;height:343px;border:2px solid var(--ink);display:flex}
.rcard{flex:1;text-align:center;padding-top:26px;border-right:1px solid var(--ink)}
.rcard:last-child{border-right:0}
.rcard.featured{background:var(--teal);color:var(--white)}
.rmeta{display:flex;justify-content:center;gap:30px;font-size:15px;color:var(--text)}
.featured .rmeta{color:var(--white)}
.rmeta span{display:flex;align-items:center;gap:8px}
.rcard h3{font-family:"Roboto",sans-serif;font-weight:500;font-size:19.5px;margin-top:22px;color:var(--ink)}
.featured h3{color:var(--white)}
.rcard p{font-size:13.5px;line-height:27.5px;width:275px;margin:18px auto 0}
.ghost{display:inline-flex;align-items:center;justify-content:center;width:155px;height:46px;margin-top:14px;border:2px solid var(--ink);border-radius:0 22px 0 22px;font-size:15px;font-weight:500;letter-spacing:.3px}
.featured .ghost{border-color:var(--white)}

/* about */
.about{left:0;top:1367px;width:643px;height:691px;background:var(--teal);border-radius:140px 0 0 140px;color:var(--white)}
.about h2{position:absolute;left:64px;top:60px;font-family:"Lato",sans-serif;font-weight:700;font-size:37px}
.about h2::after{content:"";display:block;width:114px;height:3px;background:var(--white);margin:16px 0 0 38px}
.about .copy{position:absolute;left:67px;top:148px;width:529px;font-size:17.5px;line-height:31.5px;text-align:justify}
.about .copy p{margin-bottom:14px}
.about .more{position:absolute;left:63px;top:589px;width:192px;height:54px;border:2px solid var(--white);border-radius:0 26px 0 26px;font-size:19px;font-weight:500;letter-spacing:.5px;display:flex;align-items:center;justify-content:center}
.about-art{left:643px;top:1367px;width:557px;height:691px;background:linear-gradient(90deg,#4a4a4a 0%,#9a9a9a 22%,#c84a3a 35%,#e8c23a 50%,#3a8ad0 65%,#d84aa0 80%,#2aa860 100%)}

/* blog */
.blog{top:2267px;width:302px;height:353px;background:var(--white);box-shadow:0 2px 12px rgba(0,0,0,.18);padding:23px 23px 0}
.blog.active{border-bottom:3px solid var(--blue)}
.blog.dim{background:#f3f3f3}
.badge{width:50px;height:56px;background:var(--blue);color:var(--white);font-size:16px;line-height:20px;text-align:center;padding-top:8px}
.blog h4{margin-top:20px;color:var(--ink);font-weight:700;font-size:17.5px;line-height:25px}
.blog p{margin-top:8px;color:var(--muted);font-size:15.5px;line-height:28.5px}
.blog a{display:inline-block;margin-top:6px;margin-left:4px;color:var(--blue);font-size:15.5px;text-decoration:underline}
.reports{left:431px;top:2678px;width:339px;height:51px;background:linear-gradient(90deg,var(--teal),var(--blue));color:var(--white);border-radius:0 26px 0 26px;font-size:18.5px;font-weight:500;letter-spacing:1px;display:flex;align-items:center;justify-content:center}

/* footer */
.footer{left:0;top:2831px;width:1200px;height:730px;background:var(--black);border-top-right-radius:240px 220px;color:var(--white)}
.mail-icon{position:absolute;left:575px;top:70px}
.footer h2{position:absolute;left:0;top:118px;width:1200px;text-align:center;font-family:"Lato",sans-serif;font-weight:700;font-size:29px}
.footer .sub{position:absolute;left:0;top:164px;width:1200px;text-align:center;font-size:15px}
.signup{position:absolute;left:245px;top:201px;width:710px;height:47px;background:var(--white);display:flex;align-items:center;padding:0 4px 0 23px}
.signup span{flex:1;color:var(--ink);font-size:15.5px}
.signup b{width:108px;height:39px;background:var(--teal);color:var(--white);font-size:15px;font-weight:500;display:flex;align-items:center;justify-content:center}
.rule{position:absolute;left:112px;width:978px;height:1px;background:#333}
.f-logo{position:absolute;left:112px;top:314px;width:176px;height:106px;background:var(--white);display:flex;align-items:center;justify-content:center;padding:8px}
.f-logo div{width:100%;height:100%;border:2px solid var(--teal);display:flex;align-items:center;justify-content:center;color:var(--teal);font-family:"Lato",sans-serif;font-weight:700;font-size:17px;text-align:center;line-height:1.15}
.f-about{position:absolute;left:112px;top:443px;width:310px;font-size:15.5px;line-height:24.5px}
.col{position:absolute;top:330px}
.col h5{font-family:"Lato",sans-serif;font-weight:700;font-size:20px;margin-bottom:10px}
.col a{display:block;font-size:15px;line-height:32.5px;margin-left:3px}
.social{display:flex;align-items:center;gap:11px;font-size:15px;margin-bottom:24px}
.social i{display:inline-block;width:31px;height:31px;border:2px solid var(--white);border-radius:50%}
.disc h6{position:absolute;left:112px;top:597px;font-family:"Lato",sans-serif;font-weight:700;font-size:19px}
.disc p{position:absolute;left:113px;top:629px;width:405px;font-size:13.5px;line-height:25.5px}
.copyright{position:absolute;left:691px;top:629px;font-size:15px}
</style>
</head>
<body>

<header class="abs topbar">
  <div class="abs follow">Follow Us : <i class="ring"></i><i class="ring"></i></div>
  <div class="abs email">Email Us : <span>hello@tealstoneresearch.com</span></div>
  <div class="abs call">Call Us : <span>+1 555 010 2040</span></div>
</header>

<nav class="abs nav">
  <div class="abs brand">TEALSTONE<br>RESEARCH</div>
  <div class="abs menu">
    <a class="active" href="#">HOME</a><a href="#">About</a><a href="#">Research</a><a href="#">Careers</a><a href="#" style="margin-right:30px">News</a><a href="#">Contact</a>
  </div>
  <svg class="abs search" width="16" height="16" viewBox="0 0 16 16"><circle cx="6.5" cy="6.5" r="4.5" fill="none" stroke="#111" stroke-width="2.2"/><line x1="10" y1="10" x2="14" y2="14" stroke="#111" stroke-width="2.4"/></svg>
  <a class="abs login" href="#"><svg width="12" height="13" viewBox="0 0 12 13"><circle cx="6" cy="3.5" r="3" fill="#fff"/><path d="M0 13c0-4 2.5-6 6-6s6 2 6 6z" fill="#fff"/></svg>LOG IN</a>
</nav>

<section class="abs hero" role="img" aria-label="Glowing digital coin over a dark network of connected nodes">
  <h1>WELCOME TO<br>TEALSTONE RESEARCH</h1>
  <p>Lorem ipsum dolor sit amet, consectetur adipiscing elit, sed do eiusmod tempor incididunt ut labore et dolore magna aliqua. Ut enim ad minim veniam, quis nostrud exercitation ullamco laboris</p>
  <a class="cta" href="#">GET STARTED</a>
  <span class="arrow" style="left:34px;top:302px"><svg width="12" height="14" viewBox="0 0 12 14"><path d="M9 2L3 7l6 5" fill="none" stroke="#fff" stroke-width="3"/></svg></span>
  <span class="arrow" style="left:1125px;top:302px"><svg width="12" height="14" viewBox="0 0 12 14"><path d="M3 2l6 5-6 5" fill="none" stroke="#fff" stroke-width="3"/></svg></span>
</section>

<h2 class="abs sec-title" style="top:856px">RESEARCH</h2>

<section class="abs research">
  <article class="rcard">
    <div class="rmeta"><span><svg width="15" height="15" viewBox="0 0 15 15"><rect x="1" y="2" width="13" height="12" fill="none" stroke="#333" stroke-width="1.6"/><rect x="1" y="2" width="13" height="3" fill="#333"/></svg>09.02.2022</span><span><svg width="13" height="14" viewBox="0 0 12 13"><circle cx="6" cy="3.5" r="3" fill="#333"/><path d="M0 13c0-4 2.5-6 6-6s6 2 6 6z" fill="#333"/></svg>Mara Quinlan</span></div>
    <h3>Protocol Network Valuations</h3>
    <p>Lorem ipsum dolor sit amet, consectetur adipiscing elit, sed do eiusmod tempor incididunt ut labore et dolore magna aliqua. Ut enim ad minim veniam, quis nostrud exercitation ullamco laboris nisi</p>
    <a class="ghost" href="#">GET STARTED</a>
  </article>
  <article class="rcard featured">
    <div class="rmeta"><span><svg width="15" height="15" viewBox="0 0 15 15"><rect x="1" y="2" width="13" height="12" fill="none" stroke="#fff" stroke-width="1.6"/><rect x="1" y="2" width="13" height="3" fill="#fff"/></svg>09.02.2022</span><span><svg width="13" height="14" viewBox="0 0 12 13"><circle cx="6" cy="3.5" r="3" fill="#fff"/><path d="M0 13c0-4 2.5-6 6-6s6 2 6 6z" fill="#fff"/></svg>Mara Quinlan</span></div>
    <h3>Protocol Network Valuations</h3>
    <p>Lorem ipsum dolor sit amet, consectetur adipiscing elit, sed do eiusmod tempor incididunt ut labore et dolore magna aliqua. Ut enim ad minim veniam, quis nostrud exercitation ullamco laboris nisi</p>
    <a class="ghost" href="#">GET STARTED</a>
  </article>
  <article class="rcard">
    <div class="rmeta"><span><svg width="15" height="15" viewBox="0 0 15 15"><rect x="1" y="2" width="13" height="12" fill="none" stroke="#333" stroke-width="1.6"/><rect x="1" y="2" width="13" height="3" fill="#333"/></svg>09.02.2022</span><span><svg width="13" height="14" viewBox="0 0 12 13"><circle cx="6" cy="3.5" r="3" fill="#333"/><path d="M0 13c0-4 2.5-6 6-6s6 2 6 6z" fill="#333"/></svg>Mara Quinlan</span></div>
    <h3>Protocol Network Valuations</h3>
    <p>Lorem ipsum dolor sit amet, consectetur adipiscing elit, sed do eiusmod tempor incididunt ut labore et dolore magna aliqua. Ut enim ad minim veniam, quis nostrud exercitation ullamco laboris nisi</p>
    <a class="ghost" href="#">GET STARTED</a>
  </article>
</section>

<section class="abs about">
  <h2>ABOUT US</h2>
  <div class="copy">
    <p>Lorem ipsum dolor sit amet, consectetur adipiscing elit, sed do eiusmod tempor incididunt ut labore et dolore magna aliqua. Ut enim ad minim veniam, quis nostrud exercitation ullamco laboris nisi ut aliquip ex ea commodo consequat.</p>
    <p>Duis aute irure dolor in reprehenderit in voluptate velit esse cillum dolore eu fugiat nulla pariatur. Excepteur sint occaecat cupidatat non proident, sunt in culpa qui officia deserunt mollit anim id est laborum.</p>
    <p>Duis aute irure dolor in reprehenderit in voluptate velit esse cillum dolore eu fugiat nulla pariatur. Excepteur sint occaecat cupidatat non proident, sunt in culpa qui officia deserunt mollit anim id est laborum.</p>
  </div>
  <a class="more" href="#">READ MORE</a>
</section>
<div class="abs about-art" role="img" aria-label="Street art photo: a child pulling back a grey curtain to reveal a bright graffiti wall"></div>

<h2 class="abs sec-title" style="top:2161px">LATEST BLOG</h2>

<article class="abs blog" style="left:133px">
  <div class="badge">FEB<br>10</div>
  <h4>Lorem ipsum dolor sit amet, consectetur adipiscing elit, sed do eiusmod tempor</h4>
  <p>Sed ut perspiciatis unde omnis iste laudantium, totam rem aperiam, eaque ipsa quae ab illo inventore veritatis et quasi architecto beatae</p>
  <a href="#">READ MORE</a>
</article>
<article class="abs blog active" style="left:460px">
  <div class="badge">FEB<br>10</div>
  <h4>Lorem ipsum dolor sit amet, consectetur adipiscing elit, sed do eiusmod tempor</h4>
  <p>Sed ut perspiciatis unde omnis iste laudantium, totam rem aperiam, eaque ipsa quae ab illo inventore veritatis et quasi architecto beatae</p>
  <a href="#">READ MORE</a>
</article>
<article class="abs blog dim" style="left:787px">
  <div class="badge">FEB<br>10</div>
  <h4>Lorem ipsum dolor sit amet, consectetur adipiscing elit, sed do eiusmod tempor</h4>
  <p>Sed ut perspiciatis unde omnis iste laudantium, totam rem aperiam, eaque ipsa quae ab illo inventore veritatis et quasi architecto beatae</p>
  <a href="#">READ MORE</a>
</article>

<a class="abs reports" href="#">RECENT RESEARCH REPORTS</a>

<footer class="abs footer">
  <svg class="mail-icon" width="50" height="42" viewBox="0 0 50 42"><rect x="2" y="12" width="36" height="27" fill="none" stroke="#fff" stroke-width="2.5"/><path d="M2 12l18 14 18-14" fill="none" stroke="#fff" stroke-width="2.5"/><circle cx="38" cy="12" r="10" fill="#000" stroke="#fff" stroke-width="2.5"/><path d="M42 12h-8m3-3l-3 3 3 3" fill="none" stroke="#fff" stroke-width="2"/></svg>
  <h2>Join Our Mailing List for News</h2>
  <p class="sub">Lorem ipsum dolor sit amet, consectetur adipiscing elit, sed do eiusmod tempor</p>
  <div class="signup"><span>Enter Email Address</span><b>SUBMIT</b></div>
  <div class="rule" style="top:289px"></div>
  <div class="f-logo"><div>TEALSTONE<br>RESEARCH</div></div>
  <p class="f-about">Lorem ipsum dolor sit amet, consectetur adipiscing elit, sed do eiusmod tempor incididunt ut labore et dolore magna</p>
  <div class="col" style="left:520px"><h5>USE LINK</h5><a href="#">Home</a><a href="#">About</a><a href="#">Research</a><a href="#">News</a><a href="#">Careers</a><a href="#">Contact</a></div>
  <div class="col" style="left:719px"><h5>HELP LINK</h5><a href="#">Terms&amp;condtions</a><a href="#">Privacy Policy</a><a href="#">Support</a></div>
  <div class="col" style="left:946px"><h5>FOLLOW US</h5><div class="social"><i></i>Network</div><div class="social"><i></i>Updates</div></div>
  <div class="rule" style="top:564px"></div>
  <div class="disc"><h6>Disclaimer</h6><p>We need to include the legal copy at the bottom of the main page and research page regarding not offering a security, not financial advice, etc</p></div>
  <p class="copyright">©Copyrightscrypto research &nbsp;| All Rights Reserved</p>
</footer>

</body>
</html>
```